Business card for medical clinic

I need an upmarket, modern medical/health business card for my clinic

Contact Information for Business Card

name, address, email, qr code

```html
<!DOCTYPE html>
<html lang="en">
<head>
<meta charset="utf-8">
<title>Meridian Care Clinic – Business Card</title>
<link href="https://fonts.googleapis.com/css2?family=Cinzel:wght@500&family=EB+Garamond:wght@400;500&display=swap" rel="stylesheet">
<style>
  :root {
    --backdrop: #2a2b2d;
    --navy: #1b3a63;
    --blue: #136fae;
    --sky: #1aa3e2;
    --paper: #f4f5f6;
    --ink: #3a3d42;
    --title-blue: #1a6eaa;
    --white: #ffffff;
  }
  * { margin: 0; padding: 0; box-sizing: border-box; }
  html, body {
    width: 1200px; height: 852px; overflow: hidden;
    background: var(--backdrop);
  }
  .stage {
    position: relative; width: 1200px; height: 852px;
    display: flex; align-items: center; justify-content: center; gap: 60px;
  }
  .card {
    position: relative; width: 520px; height: 300px;
    border-radius: 28px; overflow: hidden;
    box-shadow: 0 14px 30px rgba(0,0,0,.45);
  }
  .card-front {
    background: linear-gradient(120deg, var(--navy) 0%, var(--blue) 55%, var(--sky) 100%);
    display: flex; align-items: center; justify-content: center;
  }
  .brand-name {
    position: relative;
    font-family: "Cinzel", serif; font-weight: 500;
    color: var(--white); letter-spacing: 1.5px; white-space: nowrap;
  }
  .card-front .brand-name { font-size: 30px; }
  .card-back { background: var(--paper); }
  .back-art { position: absolute; inset: 0; }
  .back-brand {
    position: absolute; left: 44px; top: 50%;
    transform: translateY(-50%);
  }
  .card-back .brand-name { font-size: 21px; }
  .contact {
    position: absolute; left: 334px; top: 70px; width: 180px;
    font-family: "EB Garamond", serif; color: var(--ink);
    white-space: nowrap;
  }
  .person-name {
    font-family: "Cinzel", serif; font-weight: 500;
    font-size: 19px; color: var(--title-blue); letter-spacing: .5px;
  }
  .person-role { font-size: 13px; margin-bottom: 12px; }
  .contact-list { list-style: none; font-size: 13px; line-height: 1.55; }
  .contact-list li { display: flex; align-items: center; gap: 7px; }
  .contact-list svg { width: 11px; height: 11px; flex: none; fill: var(--ink); }
  .contact-address { margin-top: 8px; font-size: 12.5px; }
</style>
</head>
<body>
<main class="stage">
  <section class="card card-front" aria-label="Card front">
    <p class="brand-name">MERIDIAN CARE CLINIC</p>
  </section>

  <section class="card card-back" aria-label="Card back">
    <svg class="back-art" viewBox="0 0 520 300" aria-hidden="true">
      <defs>
        <linearGradient id="backBlue" x1="0" y1="0" x2="1" y2="1">
          <stop offset="0" stop-color="#1b3a63"/>
          <stop offset="1" stop-color="#1a8fd0"/>
        </linearGradient>
      </defs>
      <circle cx="-70" cy="150" r="392" fill="#1aa3e2"/>
      <circle cx="-70" cy="150" r="380" fill="url(#backBlue)"/>
    </svg>
    <div class="back-brand">
      <p class="brand-name">MERIDIAN CARE</p>
    </div>
    <div class="contact">
      <h1 class="person-name">DANIEL HALE</h1>
      <p class="person-role">Managing Director</p>
      <ul class="contact-list">
        <li><svg viewBox="0 0 12 12"><path d="M2.5 1l2 2.2-1 1.3c.7 1.5 1.8 2.6 3.3 3.3l1.3-1L10.8 8.6 9.6 10.8C5 10.4 1.6 7 1.2 2.4z"/></svg>0555-210-48810</li>
        <li><svg viewBox="0 0 12 12"><path d="M1 2.5h10v7H1z M1.5 3l4.5 3.5L10.5 3" stroke="#f4f5f6" stroke-width=".9"/></svg>info@meridiancare.com</li>
        <li><svg viewBox="0 0 12 12"><circle cx="6" cy="6" r="5"/><path d="M1 6h10M6 1v10" stroke="#f4f5f6" stroke-width=".8"/></svg>www.meridiancare.com</li>
      </ul>
      <p class="contact-address">18 Harbor Ln, Ashford, US 40210</p>
    </div>
  </section>
</main>
</body>
</html>
```